Professional looking Roller Blind Discount Card that portrays quality at a value for money price!

We need a double sided business card designed as a discount card. Size 90mm wide x 55mm high.We would like it to look professional and portray quality at a value for money price point.I have uploaded a word document with a basic layout with the information we want included on each side of the card. Please put your own thought into the layout.

Contact Information for Business Card

As per word document attached.

```html
<!DOCTYPE html>
<html lang="en">
<head>
<meta charset="utf-8">
<title>Roller Blinds Discount Card</title>
<link href="https://fonts.googleapis.com/css2?family=Poppins:wght@400;600;700&family=Anton&family=Great+Vibes&display=swap" rel="stylesheet">
<style>
  :root {
    --blue: #29a3dc;
    --blue-deep: #1a7fc4;
    --charcoal: #58595b;
    --charcoal-dark: #3a3b3d;
    --paper: #ffffff;
    --ink: #3b3b3d;
    --stage: #e6e7e9;
  }
  * { box-sizing: border-box; margin: 0; padding: 0; }
  html, body { width: 1200px; height: 874px; overflow: hidden; }
  body { background: var(--stage); font-family: "Poppins", sans-serif; position: relative; }

  .card { position: absolute; left: 280px; width: 640px; height: 391px; overflow: hidden;
          box-shadow: 0 6px 18px rgba(0,0,0,.18); }
  .card--front { top: 30px; background: var(--charcoal); }
  .card--back { top: 453px; background: var(--paper); }

  /* front */
  .front-title { position: absolute; left: 32px; top: 18px; font-weight: 700; font-size: 72px;
                 line-height: 1; color: var(--blue); letter-spacing: -0.5px; white-space: nowrap; }
  .front-subtitle { position: absolute; left: 34px; top: 100px; font-size: 28px; font-weight: 400;
                    color: var(--paper); white-space: nowrap; }
  .front-photo { position: absolute; left: 40px; top: 150px; width: 340px; height: 190px;
                 background: linear-gradient(120deg, #6b4f40 0%, #7c8a5a 40%, #4f7a3c 70%, #c9c6bf 100%); }
  .front-call { position: absolute; left: 0; top: 296px; width: 390px; height: 52px; background: var(--blue);
                color: var(--paper); font-size: 24px; display: flex; align-items: center; padding-left: 26px; gap: 8px;
                white-space: nowrap; }
  .front-call strong { font-weight: 700; }
  .fabric-bubble { position: absolute; left: 436px; top: 170px; width: 172px; height: 118px; }
  .fabric-bubble svg { display: block; }
  .fabric-bubble span { position: absolute; left: 0; top: 18px; width: 172px; text-align: center;
                        font-family: "Great Vibes", cursive; font-size: 26px; line-height: .95; color: var(--paper); }
  .brand-name { position: absolute; left: 400px; top: 330px; width: 230px; text-align: center;
                font-weight: 600; font-size: 18px; color: var(--blue); letter-spacing: 1px; white-space: nowrap; }

  /* back */
  .offer { position: absolute; left: 0; top: 14px; width: 640px; display: flex; justify-content: center;
           align-items: center; gap: 14px; }
  .offer-rule { width: 64px; height: 12px; border-top: 2px solid var(--blue); border-bottom: 2px solid var(--blue);
                position: relative; }
  .offer-rule::after { content: ""; position: absolute; left: 0; right: 0; top: 3px; border-top: 2px solid var(--blue); }
  .offer-amount { font-weight: 700; font-size: 78px; line-height: 1; color: var(--blue); white-space: nowrap; }
  .offer-detail { position: absolute; left: 0; top: 108px; width: 640px; text-align: center; color: var(--ink);
                  font-size: 24px; line-height: 1.2; }
  .offer-detail .dot { color: var(--blue); }
  .badges { position: absolute; left: 45px; top: 182px; width: 550px; display: flex; justify-content: space-between; }
  .badge { width: 140px; height: 140px; display: block; }
  .badge-word { font-family: "Anton", sans-serif; font-size: 38px; fill: var(--blue); }
  .badge-note { font-family: "Anton", sans-serif; font-size: 10px; fill: var(--paper); letter-spacing: .3px; }
  .back-band { position: absolute; left: 0; bottom: 0; width: 640px; height: 56px; background: var(--blue);
               border-top: 6px solid var(--paper); box-shadow: 0 -3px 0 #c9cacc;
               color: var(--paper); font-size: 24px; display: flex; align-items: center; justify-content: center; gap: 10px;
               white-space: nowrap; }
  .back-band strong { font-weight: 700; }
</style>
</head>
<body>

<section class="card card--front" aria-label="Card front">
  <h1 class="front-title">ROLLER BLINDS</h1>
  <p class="front-subtitle">FREE in Home Measure &amp; Quote</p>
  <div class="front-photo" role="img" aria-label="Photo of a bright room with roller-blind windows looking onto a leafy garden"></div>
  <p class="front-call">CALL <strong>0400 555 123</strong> TODAY!</p>
  <div class="fabric-bubble">
    <svg width="172" height="118" viewBox="0 0 172 118" aria-hidden="true">
      <defs>
        <linearGradient id="bubbleFill" x1="0" y1="0" x2="0" y2="1">
          <stop offset="0" stop-color="#5cc2f0"/><stop offset="1" stop-color="#1a7fc4"/>
        </linearGradient>
      </defs>
      <ellipse cx="86" cy="48" rx="84" ry="46" fill="url(#bubbleFill)"/>
      <path d="M14 70 L6 112 L40 86 Z" fill="#1a7fc4"/>
    </svg>
    <span>Huge Selection<br>of Fabrics</span>
  </div>
  <p class="brand-name">NORTHVALE PROJECTS</p>
</section>

<section class="card card--back" aria-label="Card back">
  <div class="offer">
    <span class="offer-rule"></span>
    <span class="offer-amount">25% OFF</span>
    <span class="offer-rule"></span>
  </div>
  <p class="offer-detail">Quality Custom Made Roller Blinds<br>Blockout <span class="dot">•</span> screen <span class="dot">•</span> LightFiltering</p>

  <div class="badges">
    <svg class="badge" viewBox="0 0 140 140" aria-label="Free in home measure and quote">
      <circle cx="70" cy="70" r="66" fill="var(--blue)"/>
      <rect x="4" y="50" width="132" height="44" fill="var(--charcoal-dark)"/>
      <text class="badge-word" x="70" y="82" text-anchor="middle">FREE</text>
      <text class="badge-note" x="70" y="92" text-anchor="middle">IN HOME MEASURE &amp; QUOTE</text>
    </svg>
    <svg class="badge" viewBox="0 0 140 140" aria-label="Best price guarantee">
      <circle cx="70" cy="70" r="66" fill="var(--blue)"/>
      <rect x="4" y="50" width="132" height="44" fill="var(--charcoal-dark)"/>
      <text class="badge-word" x="70" y="82" text-anchor="middle">BEST</text>
      <text class="badge-note" x="70" y="92" text-anchor="middle">PRICE GUARANTEE</text>
    </svg>
    <svg class="badge" viewBox="0 0 140 140" aria-label="Family owned and operated">
      <circle cx="70" cy="70" r="66" fill="var(--blue)"/>
      <rect x="4" y="50" width="132" height="44" fill="var(--charcoal-dark)"/>
      <text class="badge-word" x="70" y="82" text-anchor="middle" font-size="34">FAMILY</text>
      <text class="badge-note" x="70" y="92" text-anchor="middle">OWNED &amp; OPERATED</text>
    </svg>
  </div>

  <p class="back-band">CALL <strong>0400 555 123</strong> TODAY!</p>
</section>

</body>
</html>
```